Require an amazing and engaging Home Page redesign! For New Startup!

We require a new design for our home page of www.quonto.com.au.

We want this to be in a similar theme to the current site, all other pages to remain unchanged however our marketing team have advised that the current home page (initial banner) is not engaging or "hooking" potential leads. I have attached "CRO Recommendations" from our marketing team as an idea to the issues with the Quonto site.
At the moment we would only like the issues on home page reviewed (Pages: 4 to 10).

I have attached an example from our marketing team as to an idea of how the front home page needs to look.

As an idea of what our competition is doing well please view zephrimo.com.au, trevalix.com.au (great engagement on home page top banner).

Quonto is a brand new concept for Australian new car buyers. Quonto allows a customer buying a new car to receive best price offer for their new car needs and finance requirements all on a sophisticated online dashboard. The dashboard even allows the customer to interact directly with the dealerships to negotiate the price online! (never offered before).

I've provided new logo, brand guidelines for colour and font scheme.

View the website to get an idea of what Quonto is all about and let's see what we can come up with.

Thanks.

Target Market(s)

Females, age between 21-35

Industry/Entity Type

Automotive

Number of Pages Required

1 page

Requirements
Must have
• Engaging initial banner. We want to see the banner as mocked up and provided but also maybe provide an option showing a large graphic as the banner that incorporates this "hook" for engagement.
• Minimal menu (no Need Help or Newsletter buttons) with new logo on left.
• As per design mockup. Looking for engaging banner.
• Why it Works benefits section - 3 to 4 key benefits
• Customer satisfaction/testimonial area
Nice to have
• As Seen On banner or icon somewhere - maybe near or under the "Get Offers' buttons? As we have been featured in the MORNING LARK

```html
<!DOCTYPE html>
<html lang="en">
<head>
<meta charset="utf-8">
<title>Quonto – Get dealers and lenders to bid for your business</title>
<link href="https://fonts.googleapis.com/css2?family=Nunito+Sans:wght@400;600;700&display=swap" rel="stylesheet">
<style>
:root{
  --blue:#2a7aa6;
  --blue-deep:#1d6794;
  --blue-soft:#3d8fbd;
  --gold:#e3a823;
  --gold-dark:#c98f12;
  --ink:#333a40;
  --muted:#8c949a;
  --line:#d6dadd;
  --gray-bg:#f1f2f3;
  --white:#ffffff;
}
*{box-sizing:border-box;margin:0;padding:0}
html,body{width:1200px;height:3136px;overflow:hidden}
body{font-family:"Nunito Sans",Arial,sans-serif;color:var(--ink);background:var(--white);position:relative}
.abs{position:absolute}
a{color:inherit;text-decoration:none}

/* header */
.site-header{position:absolute;left:0;top:0;width:1200px;height:100px;background:var(--white);border-bottom:1px solid #e6e8ea}
.brand{position:absolute;left:100px;top:28px;display:flex;align-items:center;gap:14px}
.brand-dot{width:44px;height:44px;border-radius:50%;background:var(--gold)}
.brand-name{font-size:38px;font-weight:700;color:var(--blue)}
.main-nav{position:absolute;left:443px;top:44px;display:flex;gap:44px;font-size:18px;color:#7b8287}
.header-phone{position:absolute;left:945px;top:40px;display:flex;align-items:center;gap:10px;font-size:20px;font-weight:700;color:var(--ink)}
.phone-box{width:24px;height:24px;border-radius:4px;background:var(--gold);display:flex;align-items:center;justify-content:center}

/* hero */
.hero{position:absolute;left:0;top:100px;width:1200px;height:552px;background:linear-gradient(100deg,#e9eaec 0%,#f6f6f7 40%,#eceef0 70%,#dfe2e5 100%);border-bottom:1px solid var(--line)}
.hero-title{position:absolute;left:0;width:1200px;top:40px;text-align:center;font-size:36px;font-weight:700;color:var(--blue-deep)}
.hero-sub{position:absolute;left:0;width:1200px;top:84px;text-align:center;font-size:26px;color:var(--blue)}
.steps-card{position:absolute;left:167px;top:165px;width:991px;height:310px;background:var(--white);border-radius:18px;box-shadow:0 4px 18px rgba(0,0,0,.12)}
.hero-photo{position:absolute;left:28px;top:-32px;width:271px;height:342px;border-radius:0 0 0 18px;background:linear-gradient(180deg,#d9c3a8 0%,#b9d6ea 45%,#4fb3e6 100%)}
.step{position:absolute;top:40px;width:200px;text-align:center;font-size:16px;line-height:22px;color:#555c61}
.step-icon{width:116px;height:116px;border-radius:50%;margin:0 auto 14px;display:flex;align-items:center;justify-content:center;position:relative}
.step-num{position:absolute;left:0;top:-2px;width:38px;height:38px;border-radius:50%;border:2px solid var(--white);color:var(--white);font-size:20px;display:flex;align-items:center;justify-content:center}
.step-1 .step-icon,.step-1 .step-num{background:var(--gold)}
.step-2 .step-icon,.step-2 .step-num{background:var(--blue)}
.step-3 .step-icon,.step-3 .step-num{background:var(--blue-deep)}
.step-arrow{position:absolute;top:82px}
.slider-dots{position:absolute;top:511px;left:546px;display:flex;gap:8px}
.slider-dots span{width:14px;height:14px;border-radius:50%;background:#555}
.slider-dots span.active{background:transparent;border:2px solid #555}

/* plans */
.plans{position:absolute;left:0;top:652px;width:1200px;height:573px;background:var(--white);border-bottom:1px solid var(--line)}
.plan{position:absolute;top:84px;width:326px;height:443px;border:2px solid #d8dcdf;border-radius:10px;background:var(--white)}
.plan-price{position:absolute;left:-18px;top:-34px;width:74px;height:74px;border-radius:50%;background:var(--gold);color:var(--white);font-size:22px;font-weight:700;display:flex;align-items:center;justify-content:center}
.plan-price.blue{background:var(--blue)}
.plan-title{position:absolute;left:20px;right:20px;top:42px;text-align:center;font-size:19px;line-height:27px;color:var(--blue-deep)}
.plan-rule{position:absolute;left:140px;top:104px;width:46px;height:2px;background:#e2e5e7}
.plan-features{position:absolute;left:22px;right:18px;top:124px;list-style:none}
.plan-features li{display:flex;gap:10px;font-size:13px;line-height:18px;color:#3d4347;margin-bottom:16px}
.plan-features li svg{flex:0 0 14px;margin-top:2px}
.plan-select{position:absolute;left:22px;width:282px;height:34px;border:1px solid #c7ccd0;background:#f1f2f3;font-size:13px;color:#6b7378;padding:0 12px;display:flex;align-items:center;justify-content:space-between}
.plan-cta{position:absolute;left:22px;top:349px;width:280px;height:52px;border:2px solid var(--blue);border-radius:3px;color:var(--blue);font-size:18px;display:flex;align-items:center;justify-content:center}
.loan-btn{position:absolute;left:30px;top:272px;width:260px;height:56px;border-radius:28px;background:linear-gradient(180deg,#4f9fcc,#2371a0);color:var(--white);font-size:17px;font-weight:600;display:flex;align-items:center;justify-content:center;box-shadow:0 2px 4px rgba(0,0,0,.2)}
.popular{position:absolute;left:513px;top:70px}

/* reviews */
.reviews{position:absolute;left:0;top:1225px;width:1200px;height:437px;background:var(--gray-bg)}
.section-title{position:absolute;left:0;width:1200px;text-align:center;font-size:27px;color:var(--blue-deep)}
.review{position:absolute;top:136px;width:240px}
.stars{display:flex;gap:3px;margin-bottom:14px}
.review h3{font-size:16px;font-weight:600;color:#3a4045;margin-bottom:10px}
.review p{font-size:14px;line-height:22px;color:#9aa1a6}
.review .author{margin-top:12px;font-size:14px;font-weight:700;color:var(--blue-deep)}
.rev-arrow{position:absolute;top:186px}
.rating-note{position:absolute;left:0;width:1200px;top:374px;text-align:center;font-size:16px;color:#a3a9ad}

/* why it works */
.why-tab{position:absolute;left:466px;top:1662px;width:247px;height:54px;background:var(--blue);color:var(--white);font-size:26px;display:flex;align-items:center;justify-content:center;border-radius:3px 3px 0 0}
.why{position:absolute;left:0;top:1714px;width:1200px;height:473px;background:var(--blue)}
.benefit{position:absolute;top:110px;width:168px;text-align:center;color:var(--white);font-size:14px;line-height:22px}
.benefit-icon{height:70px;display:flex;align-items:center;justify-content:center}
.benefit-num{width:40px;height:40px;border-radius:50%;background:var(--blue-deep);border:1px solid rgba(255,255,255,.35);margin:12px auto 16px;display:flex;align-items:center;justify-content:center;font-size:20px}
.why-cta{position:absolute;left:242px;top:376px;width:152px;height:44px;border:2px solid var(--white);border-radius:22px;color:var(--white);font-size:17px;display:flex;align-items:center;justify-content:center}
.why-photo{position:absolute;left:600px;top:0;width:600px;height:473px;background:linear-gradient(120deg,#c9c4bd 0%,#8b8f93 35%,#5b6f44 65%,#7fbf3a 100%)}
.play{position:absolute;left:238px;top:178px}

/* deals */
.deals{position:absolute;left:0;top:2187px;width:1200px;height:510px;background:var(--white)}
.deals-title{position:absolute;left:0;width:1200px;top:60px;text-align:center;font-size:27px;line-height:40px;color:#2c3236}
.deal{position:absolute;top:172px;width:260px;text-align:center}
.deal-photo{width:240px;height:120px;margin:20px auto 0;border-radius:50% 50% 8px 8px / 60% 60% 8px 8px;background:linear-gradient(180deg,#e7e9eb 0%,#b9bfc4 60%,#7d858b 100%)}
.deal-badge{position:absolute;left:30px;top:0;width:76px;height:76px;border-radius:50%;background:var(--gold);color:var(--white);display:flex;flex-direction:column;align-items:center;justify-content:center;font-size:22px;font-weight:700;line-height:22px}
.deal-badge small{font-size:12px;font-weight:600}
.deal h4{margin-top:44px;font-size:18px;font-weight:600;color:var(--blue-deep)}
.deal p{margin-top:8px;font-size:13px;line-height:22px;color:#8e959a}

/* footer */
.site-footer{position:absolute;left:0;top:2697px;width:1200px;height:439px;background:var(--gold);color:var(--white)}
.f-col{position:absolute;top:60px}
.f-col h5{font-size:20px;font-weight:600;letter-spacing:1px;margin-bottom:20px}
.f-col ul{list-style:none}
.f-col li{font-size:16px;line-height:32px}
.f-divider{position:absolute;top:60px;width:1px;height:190px;background:rgba(255,255,255,.35)}
.contact-row{display:flex;gap:14px;align-items:flex-start;font-size:16px;line-height:32px}
.socials{display:flex;gap:8px;margin-top:12px}
.socials span{width:30px;height:30px;border-radius:50%;border:2px solid var(--white)}
.f-bottom{position:absolute;left:0;top:366px;width:1200px;border-top:1px solid rgba(255,255,255,.4);text-align:center;padding-top:24px;font-size:12px;color:rgba(255,255,255,.8)}
</style>
</head>
<body>

<header class="site-header">
  <div class="brand"><span class="brand-dot"></span><span class="brand-name">Quonto</span></div>
  <nav class="main-nav"><a>How it works</a><a>Pricing</a><a>FAQ</a><a>Apply</a><a>Login</a></nav>
  <div class="header-phone">
    <span class="phone-box"><svg width="14" height="14" viewBox="0 0 24 24"><path fill="#fff" d="M6.6 10.8a15 15 0 0 0 6.6 6.6l2.2-2.2c.3-.3.7-.4 1-.2 1.1.4 2.3.6 3.6.6.6 0 1 .4 1 1V20c0 .6-.4 1-1 1A17 17 0 0 1 3 4c0-.6.4-1 1-1h3.5c.6 0 1 .4 1 1 0 1.3.2 2.5.6 3.6.1.3 0 .7-.2 1z"/></svg></span>
    1300 482 916
  </div>
</header>

<section class="hero" role="img" aria-label="Softly blurred car showroom background">
  <h1 class="hero-title">A Revolution in Car Buying Has Arrived</h1>
  <p class="hero-sub">Get car dealers and lenders to bid for YOUR business today</p>
  <div class="steps-card">
    <div class="hero-photo" role="img" aria-label="Smiling young woman holding a blue cardboard car cut-out"></div>
    <div class="step step-1" style="left:390px">
      <div class="step-icon"><span class="step-num">1</span>
        <svg width="54" height="54" viewBox="0 0 24 24" fill="none" stroke="#fff" stroke-width="1.5" stroke-linejoin="round"><path d="M7 10v11H3V10zM7 10l4-7c1.5 0 2.5 1 2.2 2.6L12.6 9H19a2 2 0 0 1 2 2.3l-1.3 7.4A2 2 0 0 1 17.7 21H7"/></svg>
      </div>
      Submit You Car or<br>Finance Needs
    </div>
    <svg class="step-arrow" style="left:555px" width="60" height="30" viewBox="0 0 60 30"><path d="M4 24 Q30 0 54 14" fill="none" stroke="#9aa1a6" stroke-width="1.5"/><path d="M48 8 L55 14 L47 18" fill="none" stroke="#9aa1a6" stroke-width="1.5"/></svg>
    <div class="step step-2" style="left:597px">
      <div class="step-icon"><span class="step-num">2</span>
        <svg width="56" height="56" viewBox="0 0 24 24" fill="none" stroke="#fff" stroke-width="1.4"><circle cx="12" cy="7" r="4"/><path d="M4 22c0-5 3.5-8 8-8s8 3 8 8M12 14l-1.5 3 1.5 4 1.5-4z"/></svg>
      </div>
      Dealerships<br>and lenders submit<br>their best offers
    </div>
    <svg class="step-arrow" style="left:763px" width="60" height="30" viewBox="0 0 60 30"><path d="M4 24 Q30 0 54 14" fill="none" stroke="#9aa1a6" stroke-width="1.5"/><path d="M48 8 L55 14 L47 18" fill="none" stroke="#9aa1a6" stroke-width="1.5"/></svg>
    <div class="step step-3" style="left:803px">
      <div class="step-icon"><span class="step-num">3</span>
        <svg width="54" height="54" viewBox="0 0 24 24" fill="none" stroke="#fff" stroke-width="1.4" stroke-linejoin="round"><path d="M9 13V4.5a1.5 1.5 0 0 1 3 0V11l5 1a2 2 0 0 1 1.6 2.3L17.5 21H10l-4-5a1.5 1.5 0 0 1 2.3-2z"/><path d="M6 5a4.5 4.5 0 0 1 9 0"/></svg>
      </div>
      You choose the best<br>deal online and<br>exchange contact<br>details. It's that easy!
    </div>
  </div>
  <div class="slider-dots"><span class="active"></span><span></span><span></span><span></span></div>
</section>

<section class="plans">
  <div class="plan" style="left:86px">
    <div class="plan-price">$47</div>
    <h2 class="plan-title">I Just need the best deals<br>on a new car</h2>
    <div class="plan-rule"></div>
    <ul class="plan-features">
      <li><svg width="14" height="14" viewBox="0 0 14 14"><circle cx="7" cy="7" r="7" fill="#e3a823"/><path d="M4 7.2l2 2 4-4" stroke="#fff" stroke-width="1.6" fill="none"/></svg>3 dealership BEST PRICE car quotes</li>
    </ul>
    <div class="plan-select" style="top:248px">Car Model<svg width="12" height="8" viewBox="0 0 12 8"><path d="M1 1l5 5 5-5" stroke="#555" stroke-width="1.5" fill="none"/></svg></div>
    <div class="plan-select" style="top:294px">Car Make<svg width="12" height="8" viewBox="0 0 12 8"><path d="M1 1l5 5 5-5" stroke="#555" stroke-width="1.5" fill="none"/></svg></div>
    <a class="plan-cta">Get Offers</a>
  </div>

  <div class="plan" style="left:437px">
    <div class="plan-price blue">$47</div>
    <h2 class="plan-title">I Just need the best deals on<br>a new car and finance</h2>
    <div class="plan-rule"></div>
    <ul class="plan-features">
      <li><svg width="14" height="14" viewBox="0 0 14 14"><circle cx="7" cy="7" r="7" fill="#e3a823"/><path d="M4 7.2l2 2 4-4" stroke="#fff" stroke-width="1.6" fill="none"/></svg>3 dealership BEST PRICE car quotes</li>
      <li><svg width="14" height="14" viewBox="0 0 14 14"><circle cx="7" cy="7" r="7" fill="#e3a823"/><path d="M4 7.2l2 2 4-4" stroke="#fff" stroke-width="1.6" fill="none"/></svg>3 car finance quotes from our broker panela</li>
    </ul>
    <div class="plan-select" style="top:248px">Car Model<svg width="12" height="8" viewBox="0 0 12 8"><path d="M1 1l5 5 5-5" stroke="#555" stroke-width="1.5" fill="none"/></svg></div>
    <div class="plan-select" style="top:294px">Car Make<svg width="12" height="8" viewBox="0 0 12 8"><path d="M1 1l5 5 5-5" stroke="#555" stroke-width="1.5" fill="none"/></svg></div>
    <a class="plan-cta">Get Offers</a>
  </div>

  <svg class="popular" width="202" height="34" viewBox="0 0 202 34">
    <path d="M10 1H192L201 17L192 33H10L1 17Z" fill="#e3a823" stroke="#fff" stroke-width="2"/>
    <path d="M14 5H188L195 17L188 29H14L7 17Z" fill="none" stroke="#fff" stroke-width="1" opacity=".6"/>
    <text x="101" y="22" text-anchor="middle" font-family="Nunito Sans, Arial, sans-serif" font-size="15" font-weight="600" fill="#fff">Most Popular</text>
  </svg>

  <div class="plan" style="left:786px">
    <div class="plan-price">$7</div>
    <h2 class="plan-title">I Just need the best deals on<br>a my car finance</h2>
    <div class="plan-rule"></div>
    <ul class="plan-features" style="top:110px">
      <li><svg width="14" height="14" viewBox="0 0 14 14"><circle cx="7" cy="7" r="7" fill="#e3a823"/><path d="M4 7.2l2 2 4-4" stroke="#fff" stroke-width="1.6" fill="none"/></svg>Perfect for NEW or USED Cards</li>
      <li><svg width="14" height="14" viewBox="0 0 14 14"><circle cx="7" cy="7" r="7" fill="#e3a823"/><path d="M4 7.2l2 2 4-4" stroke="#fff" stroke-width="1.6" fill="none"/></svg>Receive up to 3 live loan quotes</li>
      <li><svg width="14" height="14" viewBox="0 0 14 14"><circle cx="7" cy="7" r="7" fill="#e3a823"/><path d="M4 7.2l2 2 4-4" stroke="#fff" stroke-width="1.6" fill="none"/></svg>Guaranteed to beat dealership finance</li>
      <li><svg width="14" height="14" viewBox="0 0 14 14"><circle cx="7" cy="7" r="7" fill="#e3a823"/><path d="M4 7.2l2 2 4-4" stroke="#fff" stroke-width="1.6" fill="none"/></svg>Quotes from our onward-winning broker panel</li>
    </ul>
    <a class="loan-btn">$ Estimated Loan Amount</a>
    <a class="plan-cta">Get Offers</a>
  </div>
</section>

<section class="reviews">
  <h2 class="section-title" style="top:56px">See What Our Customer Says</h2>
  <svg class="rev-arrow" style="left:48px" width="20" height="36" viewBox="0 0 20 36"><path d="M17 2L3 18l14 16" stroke="#b5bbbf" stroke-width="3" fill="none"/></svg>
  <svg class="rev-arrow" style="left:1130px" width="20" height="36" viewBox="0 0 20 36"><path d="M3 2l14 16L3 34" stroke="#b5bbbf" stroke-width="3" fill="none"/></svg>

  <article class="review" style="left:111px">
    <div class="stars"><svg width="88" height="16" viewBox="0 0 88 16"><g fill="none" stroke="#e3a823" stroke-width="1.2"><path id="s1" d="M8 1l2 5h5l-4 3 1.6 5L8 11l-4.6 3L5 9 1 6h5z"/><use href="#s1" x="18"/><use href="#s1" x="36"/><use href="#s1" x="54"/><use href="#s1" x="72"/></g></svg></div>
    <h3>Excellent- No Reservation</h3>
    <p>Arcu Morbi porta libero id ullamcorper nonummy nibh ligula pulvinar metus eget consectetuer augue</p>
    <div class="author">- MAYA RENSHAW</div>
  </article>
  <article class="review" style="left:370px">
    <div class="stars"><svg width="88" height="16" viewBox="0 0 88 16"><g fill="none" stroke="#e3a823" stroke-width="1.2"><path id="s2" d="M8 1l2 5h5l-4 3 1.6 5L8 11l-4.6 3L5 9 1 6h5z"/><use href="#s2" x="18"/><use href="#s2" x="36"/><use href="#s2" x="54"/><use href="#s2" x="72"/></g></svg></div>
    <h3>Awesome!</h3>
    <p>Arcu Morbi porta libero id ullamcorper nonummy nibh ligula pulvinar metus eget consectetuer augue</p>
    <div class="author">- MAYA RENSHAW</div>
  </article>
  <article class="review" style="left:638px">
    <div class="stars"><svg width="88" height="16" viewBox="0 0 88 16"><g fill="none" stroke="#e3a823" stroke-width="1.2"><path id="s3" d="M8 1l2 5h5l-4 3 1.6 5L8 11l-4.6 3L5 9 1 6h5z"/><use href="#s3" x="18"/><use href="#s3" x="36"/><use href="#s3" x="54"/><use href="#s3" x="72"/></g></svg></div>
    <h3>Professional</h3>
    <p>Arcu Morbi porta libero id ullamcorper nonummy nibh ligula pulvinar metus eget consectetuer augue</p>
    <div class="author">- MAYA RENSHAW</div>
  </article>
  <article class="review" style="left:897px">
    <div class="stars"><svg width="88" height="16" viewBox="0 0 88 16"><g fill="none" stroke="#e3a823" stroke-width="1.2"><path id="s4" d="M8 1l2 5h5l-4 3 1.6 5L8 11l-4.6 3L5 9 1 6h5z"/><use href="#s4" x="18"/><use href="#s4" x="36"/><use href="#s4" x="54"/><use href="#s4" x="72"/></g></svg></div>
    <h3>Best Customer Service</h3>
    <p>Arcu Morbi porta libero id ullamcorper nonummy nibh ligula pulvinar metus eget consectetuer augue</p>
    <div class="author">- MAYA RENSHAW</div>
  </article>
  <p class="rating-note">Rated 9.3 out of  10 based on 302 Reviews</p>
</section>

<div class="why-tab">Why it Works</div>
<section class="why">
  <div class="benefit" style="left:79px">
    <div class="benefit-icon"><svg width="70" height="70" viewBox="0 0 70 70" fill="none" stroke="#fff" stroke-width="4"><circle cx="20" cy="18" r="10"/><circle cx="50" cy="52" r="10"/><path d="M56 8L14 62"/></svg></div>
    <div class="benefit-num">1</div>
    We don't chare any middleman fees saving your between $300-$1000!
  </div>
  <div class="benefit" style="left:244px">
    <div class="benefit-icon"><svg width="66" height="66" viewBox="0 0 66 66" fill="none" stroke="#fff" stroke-width="4"><circle cx="33" cy="33" r="29"/><circle cx="33" cy="33" r="7"/><path d="M33 26V6M27 37L10 47M39 37l17 10"/></svg></div>
    <div class="benefit-num">2</div>
    Use our industry first counter offer button to negotiate with deaerships
  </div>
  <div class="benefit" style="left:414px">
    <div class="benefit-icon"><svg width="66" height="66" viewBox="0 0 66 66"><path d="M6 8h26l28 28-24 24L8 32z" fill="#fff"/><circle cx="19" cy="20" r="5" fill="#2a7aa6"/></svg></div>
    <div class="benefit-num">3</div>
    Receive discounted insurance deals after the purchase &amp; keep saving
  </div>
  <a class="why-cta">Get Offers</a>
  <div class="why-photo" role="img" aria-label="Couple shaking hands with a salesman beside a green car in a showroom">
    <svg class="play" width="96" height="96" viewBox="0 0 96 96"><circle cx="48" cy="48" r="45" fill="rgba(255,255,255,.12)" stroke="#fff" stroke-width="3"/><path d="M38 30l28 18-28 18z" fill="none" stroke="#fff" stroke-width="3" stroke-linejoin="round"/></svg>
  </div>
</section>

<section class="deals">
  <h2 class="deals-title">Live Deals- Our Average clients saved<br>Nearly 14% off list Price</h2>
  <div class="deal" style="left:90px">
    <div class="deal-badge">$89<small>/week</small></div>
    <div class="deal-photo" role="img" aria-label="Grey sports coupe"></div>
    <h4>Velora ST</h4>
    <p>interdum vel blandit sed nulla<br>In ullamcorper est eget</p>
  </div>
  <div class="deal" style="left:351px">
    <div class="deal-badge">$89<small>/week</small></div>
    <div class="deal-photo" role="img" aria-label="White hatchback"></div>
    <h4>Car Brand Name</h4>
    <p>interdum vel blandit sed nulla<br>In ullamcorper est eget</p>
  </div>
  <div class="deal" style="left:610px">
    <div class="deal-badge">$89<small>/week</small></div>
    <div class="deal-photo" role="img" aria-label="White sedan"></div>
    <h4>Car Brand Name</h4>
    <p>interdum vel blandit sed nulla<br>In ullamcorper est eget</p>
  </div>
  <div class="deal" style="left:870px">
    <div class="deal-badge">$89<small>/week</small></div>
    <div class="deal-photo" role="img" aria-label="Silver crossover"></div>
    <h4>Car Brand Name</h4>
    <p>interdum vel blandit sed nulla<br>In ullamcorper est eget</p>
  </div>
</section>

<footer class="site-footer">
  <div class="f-col" style="left:82px"><h5>COMPANY</h5><ul><li>About Us</li><li>Why We Are</li><li>Our Offers</li><li>Testimonials</li><li>Latest News</li></ul></div>
  <div class="f-divider" style="left:255px"></div>
  <div class="f-col" style="left:322px"><h5>SUBLINKS</h5><ul><li>Altricies sit amet</li><li>Porttitor mattis enim</li><li>In massa</li><li>Libero interdum</li><li>Nec interdum</li></ul></div>
  <div class="f-divider" style="left:548px"></div>
  <div class="f-col" style="left:583px"><h5>RESOURCES</h5><ul><li>Support</li><li>FAQ</li><li>Apply Now</li><li>How it Works</li><li>Contac Us</li></ul></div>
  <div class="f-divider" style="left:805px"></div>
  <div class="f-col" style="left:849px"><h5>CONTACT US</h5>
    <div class="contact-row"><svg width="16" height="32" viewBox="0 0 16 32"><path d="M8 6a6 6 0 0 0-6 6c0 4.5 6 11 6 11s6-6.5 6-11a6 6 0 0 0-6-6zm0 8.2a2.2 2.2 0 1 1 0-4.4 2.2 2.2 0 0 1 0 4.4z" fill="#fff"/></svg><span>4/F Harbourline House<br>18-20 Pellow Street</span></div>
    <div class="contact-row" style="margin-top:20px"><svg width="16" height="32" viewBox="0 0 16 32"><path d="M4.3 13.2a10 10 0 0 0 4.4 4.4l1.5-1.5c.2-.2.5-.3.7-.1.7.2 1.5.4 2.4.4.4 0 .7.3.7.7v2.3c0 .4-.3.7-.7.7A11.3 11.3 0 0 1 2 8.8c0-.4.3-.7.7-.7H5c.4 0 .7.3.7.7 0 .9.1 1.7.4 2.4.1.2 0 .5-.2.7z" fill="#fff"/></svg><span>(03) 9415 2207</span></div>
    <div class="contact-row"><svg width="16" height="32" viewBox="0 0 16 32"><path d="M1 10h14v11H1zM1 10l7 6 7-6" fill="#fff" stroke="#e3a823" stroke-width="1"/></svg><span>hello@quonto.com.au</span></div>
    <div class="socials"><span></span><span></span><span></span><span></span></div>
  </div>
  <div class="f-bottom">© 2017 Company Name  All right reserved.  Term of Use</div>
</footer>

</body>
</html>
```